LHP Regal Business Card Design 2020

Your Manor Steward is looking for a business card that is clean and straight to the point but still looks high-end and attractive. We are a team comprised of management and field professionals focused on the high-end residential marketplace. We serve homeowners and trade professionals directly based out of the Metrowest/Boston area. We provide client services as well as construction/renovation services.
We are aiming for a black and white feel (white background and black text) and a matte finish with rounded edges.

We want to emphasis our vision of "Properties - Projects - Partners".
Dana Pellham is the president of LHP

Please include the following areas we service: Boston/Cape/Newport
Please make sure to include Dana's mobile (555) 213 4480 & office number (555) 640 1937, email dana@yourmanorsteward.example and website www.yourmanorsteward.example

Colors

Designer to choose only greyscale colors for use in the design.

Requirements
Must have
• Include "Properties - Projects - Partners" in design

Include "After Hours Emergency Support # 1800 555 0142" with icon

```html
<!DOCTYPE html>
<html lang="en">
<head>
<meta charset="utf-8">
<title>LHP Business Card</title>
<link rel="stylesheet" href="https://fonts.googleapis.com/css2?family=Montserrat:wght@500;700;800&family=Work+Sans:wght@400;500&display=swap">
<style>
  :root {
    --backdrop: #161616;
    --card: #222222;
    --card-edge: #2b2b2b;
    --ink: #ffffff;
    --ink-soft: #e6e6e6;
    --accent: #b4b4b4;
  }
  * { box-sizing: border-box; margin: 0; padding: 0; }
  html, body { width: 1200px; height: 900px; overflow: hidden; }
  body {
    background: var(--backdrop);
    display: flex;
    flex-direction: column;
    align-items: center;
    justify-content: center;
    gap: 40px;
    font-family: "Work Sans", Arial, sans-serif;
    color: var(--ink);
  }
  .card {
    position: relative;
    width: 680px;
    height: 388px;
    background: linear-gradient(135deg, var(--card) 0%, var(--card-edge) 100%);
    border-radius: 6px;
    overflow: hidden;
  }
  .card::after {
    content: "";
    position: absolute;
    left: 0; right: 0; bottom: 0;
    height: 5px;
    background: var(--accent);
  }
  .wordmark {
    font-family: "Montserrat", Arial, sans-serif;
    font-weight: 800;
    color: var(--ink);
    line-height: 1;
    letter-spacing: -2px;
  }
  .company-name {
    font-family: "Montserrat", Arial, sans-serif;
    font-weight: 700;
    color: var(--ink);
    letter-spacing: 3px;
    text-transform: uppercase;
    white-space: nowrap;
  }

  /* Front */
  .card-front {
    display: flex;
    flex-direction: column;
    align-items: center;
    padding-top: 70px;
  }
  .card-front .wordmark { font-size: 130px; }
  .card-front .company-name { font-size: 22px; margin-top: 14px; }
  .service-title {
    font-family: "Montserrat", Arial, sans-serif;
    font-weight: 700;
    font-size: 20px;
    letter-spacing: 2.5px;
    margin-top: 30px;
  }
  .service-areas {
    font-family: "Montserrat", Arial, sans-serif;
    font-weight: 500;
    font-size: 18px;
    letter-spacing: 1.5px;
    margin-top: 10px;
    color: var(--ink-soft);
  }

  /* Back */
  .card-back { padding: 44px 40px 0 40px; }
  .back-main { display: flex; align-items: center; }
  .brand-block { display: flex; flex-direction: column; align-items: flex-start; }
  .brand-block .wordmark { font-size: 104px; }
  .brand-block .company-name { font-size: 15px; margin-top: 12px; letter-spacing: 2px; }
  .divider { width: 2px; height: 170px; background: var(--accent); margin: 0 26px 0 24px; flex: none; }
  .person-name {
    font-family: "Montserrat", Arial, sans-serif;
    font-weight: 700;
    font-size: 27px;
    letter-spacing: 2px;
    color: var(--accent);
    text-transform: uppercase;
  }
  .person-title { font-size: 19px; margin-top: 2px; margin-bottom: 12px; }
  .contact-list { list-style: none; }
  .contact-list li { display: flex; align-items: center; gap: 10px; font-size: 18px; line-height: 1.45; white-space: nowrap; }
  .contact-icon { width: 14px; height: 14px; flex: none; color: var(--accent); }
  .emergency-line {
    position: absolute;
    left: 0; right: 0; bottom: 88px;
    display: flex;
    justify-content: center;
    align-items: center;
    gap: 10px;
    font-size: 17px;
    color: var(--ink-soft);
  }
  .emergency-line .contact-icon { width: 18px; height: 18px; }
  .tagline {
    position: absolute;
    left: 0; right: 0; bottom: 36px;
    text-align: center;
    font-family: "Montserrat", Arial, sans-serif;
    font-weight: 700;
    font-size: 24px;
    letter-spacing: 2px;
  }
</style>
</head>
<body>

  <section class="card card-front">
    <div class="wordmark">LHP</div>
    <div class="company-name">Your Manor Steward</div>
    <div class="service-title">WE SERVICE</div>
    <div class="service-areas">BOSTON | METROWEST | SOUTH SHORE | CAPE/NEWPORT</div>
  </section>

  <section class="card card-back">
    <div class="back-main">
      <div class="brand-block">
        <div class="wordmark">LHP</div>
        <div class="company-name">Your Manor Steward</div>
      </div>
      <div class="divider"></div>
      <div class="contact-block">
        <div class="person-name">Dana Pellham</div>
        <div class="person-title">President</div>
        <ul class="contact-list">
          <li>
            <svg class="contact-icon" viewBox="0 0 16 16" fill="none" stroke="currentColor" stroke-width="1.6"><path d="M4 1.5 6 5 4.5 6.5a8 8 0 0 0 5 5L11 10l3.5 2-1 2.5C7 15 1 9 1.5 2.5z"/></svg>
            (555) 213 4480
          </li>
          <li>
            <svg class="contact-icon" viewBox="0 0 16 16" fill="none" stroke="currentColor" stroke-width="1.6"><rect x="4" y="1" width="8" height="14" rx="1.5"/><line x1="7" y1="12.5" x2="9" y2="12.5"/></svg>
            (555) 640 1937
          </li>
          <li>
            <svg class="contact-icon" viewBox="0 0 16 16" fill="none" stroke="currentColor" stroke-width="1.6"><rect x="1" y="3" width="14" height="10" rx="1"/><path d="M1 3.5 8 9l7-5.5"/></svg>
            dana@yourmanorsteward.example
          </li>
          <li>
            <svg class="contact-icon" viewBox="0 0 16 16" fill="none" stroke="currentColor" stroke-width="1.4"><circle cx="8" cy="8" r="6.5"/><ellipse cx="8" cy="8" rx="3" ry="6.5"/><line x1="1.5" y1="8" x2="14.5" y2="8"/></svg>
            www.yourmanorsteward.example
          </li>
        </ul>
      </div>
    </div>
    <div class="emergency-line">
      <svg class="contact-icon" viewBox="0 0 16 16" fill="none" stroke="currentColor" stroke-width="1.6"><path d="M8 1.5 15 14H1z"/><line x1="8" y1="6" x2="8" y2="10"/><line x1="8" y1="11.8" x2="8" y2="12.4"/></svg>
      After Hours Emergency Support # 1800 555 0142
    </div>
    <div class="tagline">PROPERTIES - PROJECTS - PARTNERS</div>
  </section>

</body>
</html>
```